Mobile Fitness snd Therapy Business Card Design

I need a business card designed for my mobile fitness and therapy business.

Please view the images that I have uploaded. I like the simplicity of the design that I have attached. I adapted it with my information

Target Market(s)

Those seeking personal training, injury rehabilitation or massage therapy.

Industry/Entity Type

Business

Contact Information for Business Card

Derek Fulham - MSc, CAT(C), RMT, CSCS, Pn2
e-mail: derek@vantrelo.com
website: www.vantrelo.com
instagram: @derek_fulham

Font styles to use
Sans Serif

Colors
3176b5
0355a3

Requirements
Must have
• "Contact us to receive a FREE assessment"
• Services offered:
• Personal Training
• Golf Fitness
• Injury Rehab
• Massage Therapy
• Yoga
Nice to have
• Consistent colours with brand
• - Dark Blue: #232837
• - Blue: #5096f0
• Consistent look/feel with the website: www.vantrelo.com

```html
<!DOCTYPE html>
<html lang="en">
<head>
<meta charset="utf-8">
<title>Vantrelo Business Card</title>
<link href="https://fonts.googleapis.com/css2?family=Roboto:wght@400;500;700&display=swap" rel="stylesheet">
<style>
  :root {
    --navy: #232837;
    --navy-light: #3a4256;
    --blue: #5096f0;
    --blue-deep: #0355a3;
    --blue-mid: #3176b5;
    --blue-pale: #7cc3f2;
    --paper: #ffffff;
    --backdrop: #e2e2e2;
  }
  * { margin: 0; padding: 0; box-sizing: border-box; }
  html, body { width: 1200px; height: 852px; overflow: hidden; }
  body {
    background: var(--backdrop);
    font-family: "Roboto", Arial, sans-serif;
    position: relative;
  }
  .card {
    position: absolute;
    top: 271px;
    width: 540px;
    height: 310px;
    border-radius: 18px;
    overflow: hidden;
    box-shadow: 0 6px 14px rgba(0,0,0,0.25);
  }
  .card-front {
    left: 40px;
    background: radial-gradient(ellipse at 55% 40%, var(--navy-light) 0%, var(--navy) 70%);
  }
  .card-back { left: 620px; background: var(--paper); }

  .front-name {
    position: absolute;
    left: 0; right: 0; top: 122px;
    text-align: center;
    color: var(--paper);
    font-weight: 500;
    font-size: 54px;
    letter-spacing: 6px;
  }

  .back-shapes { position: absolute; inset: 0; }

  .back-brand {
    position: absolute;
    right: 30px; top: 26px;
    color: var(--navy);
    font-weight: 500;
    font-size: 32px;
    letter-spacing: 3px;
  }
  .offer {
    position: absolute;
    right: 30px; top: 70px;
    text-align: right;
    color: var(--navy);
    font-size: 13px;
    line-height: 16px;
  }
  .offer .free { color: var(--blue-mid); }

  .edge-dot {
    position: absolute;
    left: -16px; top: 120px;
    width: 32px; height: 32px;
    border-radius: 50%;
    background: var(--blue-mid);
  }
  .person { position: absolute; left: 42px; top: 112px; }
  .person-name {
    color: var(--navy);
    font-weight: 700;
    font-size: 22px;
    letter-spacing: 0.5px;
  }
  .person-creds {
    color: var(--blue-mid);
    font-size: 12.5px;
    margin-top: 2px;
  }

  .contacts {
    position: absolute;
    left: 40px; top: 196px;
    list-style: none;
    color: var(--navy);
    font-size: 13.5px;
  }
  .contacts li {
    display: flex;
    align-items: center;
    gap: 7px;
    height: 18px;
  }
  .contacts svg { width: 13px; height: 13px; flex: none; }
  .contacts .accent { color: var(--blue-mid); }

  .services {
    position: absolute;
    right: 26px; top: 150px;
    text-align: right;
    color: var(--paper);
    font-size: 12px;
    line-height: 17px;
  }
  .services-title {
    color: var(--blue);
    font-weight: 700;
    font-size: 14px;
    margin-bottom: 1px;
  }
  .services .mark { color: var(--blue); }
</style>
</head>
<body>

<section class="card card-front" aria-label="Card front">
  <div class="front-name">VANTRELO</div>
</section>

<section class="card card-back" aria-label="Card back">
  <svg class="back-shapes" viewBox="0 0 540 310" preserveAspectRatio="none" aria-hidden="true">
    <path d="M0,292 C90,300 150,292 190,282 C140,302 80,310 0,310 Z" fill="var(--blue-pale)"/>
    <path d="M0,300 C80,306 140,302 180,294 L190,310 L0,310 Z" fill="var(--blue-mid)" opacity="0.6"/>
    <path d="M540,124 C440,134 345,150 318,200 C290,255 235,296 130,310 L540,310 Z" fill="var(--navy)"/>
    <path d="M540,115 C436,125 338,142 309,194 C280,250 222,292 112,310" fill="none" stroke="var(--blue-mid)" stroke-width="5"/>
    <path d="M540,106 C430,116 330,134 300,188 C270,246 205,288 92,310" fill="none" stroke="var(--blue)" stroke-width="1.5" opacity="0.6"/>
  </svg>

  <div class="back-brand">VANTRELO</div>
  <p class="offer">Contact us to receive a<br><span class="free">FREE</span> assessment</p>

  <div class="edge-dot"></div>
  <div class="person">
    <div class="person-name">DEREK FULHAM</div>
    <div class="person-creds">MSc, CAT(C), RMT, CSCS, Pn2</div>
  </div>

  <ul class="contacts">
    <li>
      <svg viewBox="0 0 14 14"><circle cx="7" cy="7" r="6.3" fill="none" stroke="#3176b5" stroke-width="1.2"/><path d="M4.6 3.8l1.4 0 .6 1.6-.9.7c.4.9 1 1.5 1.9 1.9l.7-.9 1.6.6 0 1.4c-3 .3-5.6-2.3-5.3-5.3z" fill="#3176b5"/></svg>
      250-555-0148
    </li>
    <li>
      <svg viewBox="0 0 14 14"><rect x="1.5" y="3" width="11" height="8" rx="1" fill="none" stroke="#3176b5" stroke-width="1.2"/><path d="M1.8 3.4L7 7.6l5.2-4.2" fill="none" stroke="#3176b5" stroke-width="1.2"/></svg>
      derek@vantrelo.com
    </li>
    <li>
      <svg viewBox="0 0 14 14"><circle cx="7" cy="7" r="5.8" fill="none" stroke="#3176b5" stroke-width="1.2"/><ellipse cx="7" cy="7" rx="2.4" ry="5.8" fill="none" stroke="#3176b5" stroke-width="1"/><path d="M1.2 7h11.6" stroke="#3176b5" stroke-width="1"/></svg>
      <span>www.<span class="accent">vantrelo</span>.com</span>
    </li>
    <li>
      <svg viewBox="0 0 14 14"><circle cx="7" cy="7" r="5.8" fill="none" stroke="#3176b5" stroke-width="1.2"/></svg>
      @derek_fulham
    </li>
  </ul>

  <div class="services">
    <div class="services-title">Services offered:</div>
    <div>Personal Training <span class="mark">«</span></div>
    <div>Massage Therapy <span class="mark">«</span></div>
    <div>Yoga <span class="mark">«</span> Golf Fitness <span class="mark">«</span></div>
    <div>Nutrition Coaching <span class="mark">«</span> Injury Rehab.</div>
  </div>
</section>

</body>
</html>
```